Harborline Auto LLC

Car Dealer Customer Service
Address: 2874 Cresthaven Road, Shelbyville, TN 37162
web: www.harborlineautoxq.net
email: harborlineautoxq@mailnest.example
Phone: (931) 555-0148
Phone: (629) 555-0173

```html
<!DOCTYPE html>
<html lang="en">
<head>
<meta charset="utf-8">
<title>Harborline Auto LLC – Business Card</title>
<link href="https://fonts.googleapis.com/css2?family=Montserrat:wght@400;500;800&display=swap" rel="stylesheet">
<style>
  :root {
    --page: #e9eaec;
    --card: #ffffff;
    --brand-blue: #1f78b4;
    --accent-blue: #2b8fd3;
    --accent-gold: #ebb23c;
    --ink: #1a1a1a;
  }
  * { box-sizing: border-box; margin: 0; padding: 0; }
  html, body {
    width: 1200px; height: 900px; overflow: hidden;
    background: var(--page);
    font-family: "Montserrat", sans-serif;
  }
  .canvas { position: relative; width: 1200px; height: 900px; }
  .card {
    position: absolute; left: 250px; width: 700px; height: 400px;
    background: var(--card);
    box-shadow: 0 6px 18px rgba(0,0,0,0.12);
    overflow: hidden;
  }
  .card--front { top: 40px; }
  .card--back { top: 465px; }

  .brand {
    display: flex; align-items: center; gap: 16px;
    font-weight: 800; color: var(--brand-blue);
    text-transform: uppercase; letter-spacing: 1px;
  }
  .brand__dot {
    width: 34px; height: 34px; border-radius: 50%;
    background: var(--accent-gold); flex: none;
  }
  .card--front .brand {
    position: absolute; inset: 0; justify-content: center; font-size: 40px;
  }
  .card--back .brand {
    position: absolute; left: 40px; top: 172px; font-size: 27px; gap: 12px;
  }
  .card--back .brand__dot { width: 26px; height: 26px; }

  .divider {
    position: absolute; left: 378px; top: 110px; width: 2px; height: 180px;
    background: var(--accent-blue);
  }
  .contact {
    position: absolute; left: 400px; top: 96px; color: var(--ink);
    font-size: 14.5px; font-weight: 500; line-height: 1.45;
  }
  .contact__role { margin-bottom: 14px; }
  .contact__address { margin-bottom: 14px; }
  .contact__list { list-style: none; }
  .contact__list li { display: flex; align-items: center; gap: 10px; font-size: 13.5px; }
  .contact__list svg { width: 14px; height: 14px; flex: none; fill: var(--accent-blue); }
  .contact__highlight { color: var(--accent-blue); }

  .stripe {
    position: absolute; bottom: 0; height: 14px;
  }
  .stripe--gold {
    left: 0; width: 380px; background: var(--accent-gold);
    clip-path: polygon(0 0, 100% 0, 97% 100%, 0 100%);
  }
  .stripe--blue {
    left: 372px; right: 0; background: var(--accent-blue);
    clip-path: polygon(3% 0, 100% 0, 100% 100%, 0 100%);
    margin-left: 12px;
  }
</style>
</head>
<body>
<main class="canvas">
  <section class="card card--front" aria-label="Card front">
    <div class="brand"><span class="brand__dot"></span><span>Harborline Auto</span></div>
  </section>

  <section class="card card--back" aria-label="Card back">
    <div class="brand"><span class="brand__dot"></span><span>Harborline Auto</span></div>
    <div class="divider"></div>
    <div class="contact">
      <p class="contact__role">Car Dealer Customer Service</p>
      <p class="contact__address">2874 Cresthaven Road,<br>Shelbyville, TN 37162</p>
      <ul class="contact__list">
        <li>
          <svg viewBox="0 0 24 24" aria-hidden="true"><path d="M6.6 10.8a15 15 0 0 0 6.6 6.6l2.2-2.2c.3-.3.7-.4 1-.2 1.1.4 2.3.6 3.6.6.6 0 1 .4 1 1V20c0 .6-.4 1-1 1A17 17 0 0 1 3 4c0-.6.4-1 1-1h3.5c.6 0 1 .4 1 1 0 1.3.2 2.5.6 3.6.1.3 0 .7-.2 1z"/></svg>
          (931) 555-0148
        </li>
        <li>
          <svg viewBox="0 0 24 24" aria-hidden="true"><path d="M3 8c0-2 4-4 9-4s9 2 9 4v2h-5V8H8v2H3zM6 12h12l2 8H4zm6 2a2 2 0 1 0 0 4 2 2 0 0 0 0-4z"/></svg>
          (629) 555-0173
        </li>
        <li>
          <svg viewBox="0 0 24 24" aria-hidden="true"><path d="M2 5h20v14H2zm2 2v.5l8 5 8-5V7l-8 5z"/></svg>
          harborlineautoxq@mailnest.example
        </li>
        <li>
          <svg viewBox="0 0 24 24" aria-hidden="true"><path d="M12 2a10 10 0 1 0 0 20 10 10 0 0 0 0-20zm0 2c1.2 1.5 2 3.6 2.2 6H9.8C10 7.6 10.8 5.5 12 4zM4.1 13h3.7c.1 2.2.7 4.2 1.6 5.6A8 8 0 0 1 4.1 13zm0-2a8 8 0 0 1 5.3-5.6c-.9 1.4-1.5 3.4-1.6 5.6zm5.7 2h4.4c-.2 2.4-1 4.5-2.2 6-1.2-1.5-2-3.6-2.2-6zm4.8 5.6c.9-1.4 1.5-3.4 1.6-5.6h3.7a8 8 0 0 1-5.3 5.6zm1.6-7.6c-.1-2.2-.7-4.2-1.6-5.6a8 8 0 0 1 5.3 5.6z"/></svg>
          <span>www.<span class="contact__highlight">harborlineautoxq</span>.net</span>
        </li>
      </ul>
    </div>
    <div class="stripe stripe--gold"></div>
    <div class="stripe stripe--blue"></div>
  </section>
</main>
</body>
</html>
```